Travel Agency Website - Simple General

Need a 7 page simple design that is pretty repetitive. Need to be able to load quickly that is SEO optimized. Trying to give ideas on what they can do, be personal as we are local, but at the same time come across as professional and get information easily with little burden.

- Landing Page
- Brimwell Vacations Page
- Family Trips
- Road Trips from Texas
- Other Destinations
- About Us Page
- Contact Us Page

Target Market(s)

Families

Coding

Coded - Design and coding required

Number of Pages Required

5+ page

Colors

Designer to choose colors to be used in the design.

Requirements
Must have
• Like it to flow easily with our logo. Use that for colors, etc.

```html
<!DOCTYPE html>
<html lang="en">
<head>
<meta charset="utf-8">
<title>Family Trips – Lantern Lane Travel Co.</title>
<link href="https://fonts.googleapis.com/css2?family=Poppins:wght@400;500;600;700&display=swap" rel="stylesheet">
<style>
:root{
  --gold:#b9812f;
  --teal:#094c5c;
  --teal-dark:#083f4c;
  --paper:#e9e8e4;
  --card:#f6f6f6;
  --line:#d9dde0;
  --white:#ffffff;
}
*{box-sizing:border-box;margin:0;padding:0}
html,body{width:841px;height:1200px;overflow:hidden}
body{position:relative;font-family:'Poppins',sans-serif;background:var(--white);color:var(--teal)}
.topbar{position:absolute;left:0;top:0;width:841px;height:44px;background:var(--paper)}
.topbar .phone{position:absolute;left:133px;top:13px;font-size:12px;font-weight:600;color:var(--teal);display:flex;align-items:center;gap:5px}
.brand{position:absolute;left:370px;top:6px;width:101px;height:46px;display:flex;align-items:center;justify-content:center;gap:5px;font-size:10px;font-weight:600;color:var(--teal);background:var(--white);border-radius:10px;z-index:3;text-align:center;line-height:1.1}
.brand .dot{width:8px;height:8px;border-radius:50%;background:var(--gold);flex:none}
.social-top{position:absolute;right:133px;top:16px;display:flex;gap:16px}
.social-top span{width:11px;height:11px;border:1.5px solid var(--gold)}
.social-top span.c{border-radius:50%}
.navband{position:absolute;left:0;top:44px;width:841px;height:36px;background:var(--gold)}
.navband::before,.navband::after{content:"";position:absolute;left:0;right:0;border-top:1px dashed rgba(255,255,255,.75)}
.navband::before{top:4px}.navband::after{bottom:4px}
.nav{position:absolute;top:14px;left:0;width:841px;display:flex;justify-content:center;gap:22px;font-size:7.3px;color:var(--white);letter-spacing:.2px}
.hero{position:absolute;left:0;top:80px;width:841px;height:240px;background:linear-gradient(180deg,#9b8a86 0%,#c7a98f 18%,#2f7b84 38%,#3d8c8f 55%,#b9a595 75%,#d4bfae 100%)}
.hero h1{position:absolute;top:76px;width:100%;text-align:center;font-size:22px;font-weight:700;color:var(--white)}
.hero p{position:absolute;top:113px;width:100%;text-align:center;font-size:6.4px;color:var(--white)}
.tear{position:absolute;left:0;width:841px}
.gallery{position:absolute;left:92px;top:384px;display:flex;gap:5.5px}
.gallery div{width:105px;height:105px;border-radius:7px}
.form-card{position:absolute;left:126px;top:528px;width:589px;height:503px;background:var(--card);border-radius:12px}
.form-title{position:absolute;left:143px;top:551px;width:554px;height:43px;background:var(--teal);border-radius:12px;color:var(--white);font-size:14px;font-weight:700;text-align:center;line-height:43px}
.field{position:absolute;left:149px;width:551px;height:36px;background:var(--white);border:1px solid var(--line);border-radius:8px;font-size:7px;color:var(--teal);padding:0 12px;display:flex;align-items:center;justify-content:space-between}
.field.area{align-items:flex-start;padding-top:13px}
.label{position:absolute;left:161px;font-size:7px;font-weight:600;color:var(--teal)}
.submit{position:absolute;left:143px;top:974px;width:557px;height:43px;background:var(--gold);border-radius:14px;color:var(--white);font-size:14px;font-weight:700;text-align:center;line-height:43px}
.footer{position:absolute;left:0;top:1075px;width:841px;height:125px;background:var(--teal)}
.footer-brand{position:absolute;left:106px;top:1095px;width:100px;height:84px;background:var(--white);border-radius:14px;display:flex;align-items:center;justify-content:center;gap:5px;font-size:10px;font-weight:600;color:var(--teal);text-align:center;line-height:1.15}
.footer-brand .dot{width:8px;height:8px;border-radius:50%;background:var(--gold);flex:none}
.contact{position:absolute;left:310px;top:1115px;display:flex;align-items:center;font-size:7px;color:var(--white)}
.contact .sep{width:1px;height:14px;background:rgba(255,255,255,.25);margin:0 20px}
.contact span{display:flex;align-items:center;gap:4px}
.social-foot{position:absolute;left:711px;top:1115px;display:flex;gap:4px}
.social-foot span{width:13px;height:13px;border-radius:50%;background:var(--gold)}
.rule{position:absolute;left:303px;top:1141px;width:446px;border-top:1px solid rgba(255,255,255,.15)}
.copy{position:absolute;left:310px;top:1151px;font-size:7px;color:var(--white)}
.legal{position:absolute;right:92px;top:1151px;font-size:7px;color:var(--white);word-spacing:2px}
</style>
</head>
<body>
<header class="topbar">
  <div class="phone"><svg width="11" height="11" viewBox="0 0 24 24"><path fill="#b9812f" d="M6.6 10.8a15 15 0 0 0 6.6 6.6l2.2-2.2c.3-.3.7-.4 1-.2 1.1.4 2.3.6 3.6.6.6 0 1 .4 1 1V20c0 .6-.4 1-1 1A17 17 0 0 1 3 4c0-.6.4-1 1-1h3.5c.6 0 1 .4 1 1 0 1.3.2 2.5.6 3.6.1.3 0 .7-.2 1z"/></svg>555.014.2290</div>
  <div class="brand"><span class="dot"></span>Lantern Lane<br>Travel Co.</div>
  <div class="social-top"><span class="c"></span><span></span></div>
</header>
<nav class="navband">
  <div class="nav"><span>HOME</span><span>BRIMWELL VACATIONS</span><span>FAMILY TRIPS</span><span>TEXAS ROAD TRIPS</span><span>OTHER DESTINATIONS</span><span>ABOUT US</span><span>CONTACT</span></div>
</nav>
<section class="hero" role="img" aria-label="Sunset over a tropical beach with waves on the sand">
  <h1>Family Trips</h1>
  <p>Discover amazing family trips designed to create unforgettable memories. Choose your preferred trip and we'll handle the rest.</p>
</section>
<svg class="tear" style="top:280px" height="50" viewBox="0 0 841 50" preserveAspectRatio="none"><path fill="#fff" d="M0 18 L40 14 L70 20 L110 11 L150 16 L190 8 L230 14 L260 10 L300 12 L340 6 L380 13 L420 9 L460 14 L500 7 L540 12 L580 9 L620 15 L660 11 L700 17 L740 13 L780 22 L810 17 L841 20 L841 50 L0 50Z"/></svg>

<div class="gallery">
  <div role="img" aria-label="Desert highway through red rock canyon" style="background:linear-gradient(160deg,#a06a55,#3e3a3a)"></div>
  <div role="img" aria-label="Hiker overlooking mountain valley" style="background:linear-gradient(160deg,#4d7fc4,#6e7a6a)"></div>
  <div role="img" aria-label="Calm beach at sunrise" style="background:linear-gradient(180deg,#c9c4bf,#e6cdb0 55%,#7cc3c0)"></div>
  <div role="img" aria-label="Travelers walking with suitcases on a city street" style="background:linear-gradient(160deg,#8b8a86,#4b5058)"></div>
  <div role="img" aria-label="Family taking a photo at the seaside" style="background:linear-gradient(160deg,#c9cfd3,#b9844c)"></div>
  <div role="img" aria-label="Backpack on rocks above turquoise water" style="background:linear-gradient(160deg,#22a7b4,#2d5a63)"></div>
</div>

<section class="form-card"></section>
<div class="form-title">Trip Inquiry Form</div>
<div class="field" style="top:607px">Which Trip Are You Interested In?<svg width="6" height="4" viewBox="0 0 6 4"><path d="M.5.5 3 3 5.5.5" stroke="#094c5c" fill="none"/></svg></div>
<div class="field" style="top:651px">How Many People in Your Party?</div>
<div class="label" style="top:694px">Start Date</div>
<div class="field" style="top:705px">mm/dd/yyyy<svg width="6" height="6" viewBox="0 0 6 6"><rect x=".5" y="1" width="5" height="4.5" fill="none" stroke="#000" stroke-width=".8"/><rect x=".5" y="1" width="5" height="1.4"/></svg></div>
<div class="label" style="top:748px">End Date</div>
<div class="field" style="top:759px">mm/dd/yyyy<svg width="6" height="6" viewBox="0 0 6 6"><rect x=".5" y="1" width="5" height="4.5" fill="none" stroke="#000" stroke-width=".8"/><rect x=".5" y="1" width="5" height="1.4"/></svg></div>
<div class="field" style="top:803px">What Kind of Trip?<svg width="6" height="4" viewBox="0 0 6 4"><path d="M.5.5 3 3 5.5.5" stroke="#094c5c" fill="none"/></svg></div>
<div class="field area" style="top:848px;height:116px">Any additional notes</div>
<div class="submit">Submit Trip Request</div>

<svg class="tear" style="top:1050px" height="28" viewBox="0 0 841 28" preserveAspectRatio="none"><path fill="#094c5c" d="M0 20 L40 16 L80 18 L120 12 L160 15 L200 9 L240 14 L280 10 L320 13 L360 18 L400 12 L440 15 L480 9 L520 13 L560 10 L600 14 L640 11 L680 16 L720 12 L750 3 L780 8 L810 6 L841 9 L841 28 L0 28Z"/></svg>
<footer class="footer"></footer>
<div class="footer-brand"><span class="dot"></span>Lantern Lane<br>Travel Co.</div>
<div class="contact">
  <span><svg width="7" height="7" viewBox="0 0 24 24"><path fill="#fff" d="M6.6 10.8a15 15 0 0 0 6.6 6.6l2.2-2.2c.3-.3.7-.4 1-.2 1.1.4 2.3.6 3.6.6.6 0 1 .4 1 1V20c0 .6-.4 1-1 1A17 17 0 0 1 3 4c0-.6.4-1 1-1h3.5c.6 0 1 .4 1 1 0 1.3.2 2.5.6 3.6.1.3 0 .7-.2 1z"/></svg>555.014.2290</span>
  <span class="sep"></span>
  <span><svg width="7" height="6" viewBox="0 0 14 10"><rect width="14" height="10" rx="1" fill="#fff"/><path d="M0 1 7 6 14 1" stroke="#094c5c" fill="none"/></svg>hello@lanternlanetravel.com</span>
</div>
<div class="social-foot"><span></span><span></span></div>
<div class="rule"></div>
<div class="copy">2026 Lantern Lane Travel Co. All Right Reserved</div>
<div class="legal">Terms &amp; | Conditions | Privacy Policy</div>
</body>
</html>
```